Business card

We need a business card design for our company based in Auckland , New Zealand called 'Kestrel Hall Design Ltd'. We provide architectural services. We would like to see designs that use the max. three colours (such as white, black, grey) The final design should communicate financial safety and growth."
Also I will provide our company logo. I would like to the logo to be embeded onto our business card.

Target Market(s)

new residential house, alteration & addition & light commericila design & drafting service

Industry/Entity Type

Architecture

Contact Information for Business Card

Company name: Kestrel Hall Design Ltd.
Name: Mark Delford
Job title: architectural designer & Design LBP
email address: mark@kestrelhall.co.nz
mobile number: 02 5163 2290
web site: www.kestrelhall.co.nz

Requirements
Must have
• My project must have..
• - embeded logo (attached company logo)
• I don't have a bigger version for our company logo, but I have one old one, so you can remove the word from it)
• - insert the attached small BKTW logo & LBP logo
• - creative, simple and clear business card.
• - Max. three colours
Nice to have
• - Here are the samples I would like to share with you: http://www.plimvora.com/blog/minimalistic-business-card-designs/
• I would like to have my business card like one of the creation.
Should not have
• TBA

```html
<!DOCTYPE html>
<html lang="en">
<head>
<meta charset="utf-8">
<title>Kestrel Hall Design Ltd — Business Card</title>
<link rel="stylesheet" href="https://fonts.googleapis.com/css2?family=Source+Sans+3:wght@300;400;600&display=swap">
<style>
  :root {
    --backdrop: #3b3431;
    --card: #0d0d0d;
    --card-edge: #1c1c1c;
    --ink: #f2f2f2;
    --ink-soft: #cfcfcf;
    --grey: #6e6e6e;
    --rule: #3a3a3a;
  }
  * { box-sizing: border-box; margin: 0; padding: 0; }
  html, body {
    width: 1200px; height: 900px; overflow: hidden;
    background: var(--backdrop);
    font-family: "Source Sans 3", sans-serif;
  }
  .stage {
    position: relative; width: 1200px; height: 900px;
    display: flex; align-items: center; justify-content: center; gap: 48px;
  }
  .card {
    position: relative; width: 525px; height: 300px;
    background: var(--card);
    border: 1px solid var(--card-edge);
    box-shadow: 0 14px 30px rgba(0,0,0,.45);
    color: var(--ink);
  }

  /* Front: contact side */
  .card-front { display: flex; }
  .brand-panel {
    width: 270px; height: 100%;
    display: flex; align-items: center; justify-content: center; gap: 12px;
  }
  .brand-dot {
    width: 14px; height: 14px; border-radius: 50%; background: var(--ink); flex: none;
  }
  .brand-name {
    font-weight: 300; font-size: 22px; letter-spacing: .04em; color: var(--ink);
    white-space: nowrap;
  }
  .divider {
    width: 1px; align-self: stretch; margin: 34px 0; background: var(--rule);
  }
  .contact-panel { padding: 58px 0 0 26px; }
  .person-name { font-weight: 600; font-size: 17px; line-height: 1.1; }
  .person-title { font-weight: 400; font-size: 13px; color: var(--ink-soft); margin-bottom: 28px; white-space: nowrap; }
  .contact-list { list-style: none; }
  .contact-list li {
    display: flex; align-items: center; gap: 10px;
    font-size: 14px; line-height: 21px; color: var(--ink-soft); white-space: nowrap;
  }
  .contact-list svg { width: 11px; height: 11px; fill: var(--ink); flex: none; }

  /* Back: brand side */
  .card-back {
    display: flex; flex-direction: column; align-items: center; padding-top: 92px;
  }
  .back-brand { display: flex; align-items: center; gap: 12px; }
  .back-brand .brand-name { font-size: 24px; color: var(--ink-soft); }
  .badges { display: flex; align-items: center; gap: 28px; margin-top: 46px; }
  .badge-member {
    width: 54px; height: 60px; background: var(--grey);
  }
  .badge-practitioner {
    width: 70px; height: 70px; border-radius: 50%; background: var(--ink);
  }
</style>
</head>
<body>
<main class="stage">

  <section class="card card-front" aria-label="Business card front">
    <div class="brand-panel">
      <span class="brand-dot" aria-hidden="true"></span>
      <span class="brand-name">Kestrel Hall</span>
    </div>
    <div class="divider"></div>
    <div class="contact-panel">
      <h1 class="person-name">Mark Delford</h1>
      <p class="person-title">Architectural designer &amp; Design LBP</p>
      <ul class="contact-list">
        <li>
          <svg viewBox="0 0 24 24" aria-hidden="true"><path d="M6.6 10.8a15.1 15.1 0 0 0 6.6 6.6l2.2-2.2a1 1 0 0 1 1-.25 11.4 11.4 0 0 0 3.6.57 1 1 0 0 1 1 1V20a1 1 0 0 1-1 1A17 17 0 0 1 3 4a1 1 0 0 1 1-1h3.5a1 1 0 0 1 1 1 11.4 11.4 0 0 0 .57 3.6 1 1 0 0 1-.25 1z"/></svg>
          02 5163 2290
        </li>
        <li>
          <svg viewBox="0 0 24 24" aria-hidden="true"><path d="M2 5h20v14H2z M4 7v.5l8 5 8-5V7l-8 5z" fill-rule="evenodd"/></svg>
          mark@kestrelhall.co.nz
        </li>
        <li>
          <svg viewBox="0 0 24 24" aria-hidden="true"><circle cx="12" cy="12" r="10"/></svg>
          www.kestrelhall.co.nz
        </li>
      </ul>
    </div>
  </section>

  <section class="card card-back" aria-label="Business card back">
    <div class="back-brand">
      <span class="brand-dot" aria-hidden="true"></span>
      <span class="brand-name">Kestrel Hall Design Ltd.</span>
    </div>
    <div class="badges">
      <div class="badge-member" role="img" aria-label="Professional member badge"></div>
      <div class="badge-practitioner" role="img" aria-label="Licensed building practitioner badge"></div>
    </div>
  </section>

</main>
</body>
</html>
```